Home Security Company Business Card

Looking for a eye catching business card that is non traditional and stands out but yet still looks professional. It should include all the pertinent information such as name, title, address, telephone, e-mail, website address should definitely stand out and then finally the logo.

Target Market(s)

Residential and Commercial accounts mostly upscale accounts

Industry/Entity Type

Security

Contact Information for Business Card

Name
Title
Address
Office #
Cell #
E-mail
Website

Font styles to use
Serif
Sans Serif

Requirements
Must have
• Logo, two sided color configuration
Nice to have
• You decide
Should not have
• There really aren't any.

```html
<!DOCTYPE html>
<html lang="en">
<head>
<meta charset="utf-8">
<title>Halden Home Security – Business Card</title>
<link rel="stylesheet" href="https://fonts.googleapis.com/css2?family=Source+Sans+3:wght@400;600&display=swap">
<style>
  :root {
    --backdrop: #3b3b3b;
    --card: #f7f7f7;
    --brand-red: #6c0f00;
    --brand-gold: #d3861e;
    --ink: #3c3c3c;
  }
  * { box-sizing: border-box; margin: 0; padding: 0; }
  html, body {
    width: 1200px; height: 750px; overflow: hidden;
    background: var(--backdrop);
    font-family: "Source Sans 3", Arial, sans-serif;
  }
  .canvas { position: relative; width: 1200px; height: 750px; }
  .card {
    position: absolute; top: 228px;
    width: 462px; height: 262px;
    background: var(--card);
    overflow: hidden;
  }
  .card--front { left: 124px; }
  .card--back { left: 618px; }

  .brand-band {
    position: absolute; top: 0; right: 0;
    width: 101px; height: 100%;
    background: var(--brand-red);
  }
  .wordmark {
    position: absolute; left: 34px; top: 34px;
    font-weight: 600; font-size: 21px; line-height: 1;
    letter-spacing: 0.5px; text-transform: uppercase;
    color: var(--brand-red);
  }
  .holder { position: absolute; left: 34px; top: 88px; }
  .holder__name { font-weight: 600; font-size: 17px; color: var(--brand-red); line-height: 1.2; }
  .holder__title { font-size: 12.5px; color: var(--brand-gold); line-height: 1.3; }
  .address {
    position: absolute; left: 34px; top: 130px;
    font-size: 11.5px; line-height: 14px; color: var(--ink);
  }
  .contacts { position: absolute; left: 34px; top: 166px; list-style: none; }
  .contacts li {
    display: flex; align-items: center; gap: 6px;
    height: 17.5px; font-size: 11.5px; color: var(--ink);
  }
  .contacts svg { width: 11px; height: 11px; fill: var(--brand-red); flex: none; }

  .back-mark {
    position: absolute; left: 0; top: 0; width: 100%; height: 100%;
    display: flex; align-items: center; justify-content: center; gap: 10px;
  }
  .back-mark__dot { width: 34px; height: 34px; border-radius: 50%; background: var(--brand-red); }
  .back-mark__name {
    font-weight: 600; font-size: 19px; letter-spacing: 0.5px;
    text-transform: uppercase; color: var(--brand-red);
  }
</style>
</head>
<body>
<main class="canvas">
  <section class="card card--front">
    <div class="brand-band"></div>
    <div class="wordmark">Halden Home<br>Security Inc.</div>
    <div class="holder">
      <p class="holder__name">Daniel Whitmore</p>
      <p class="holder__title">CEO/Founder</p>
    </div>
    <p class="address">4120 Birchwood Court<br>Fairbanks, Alaska 99701</p>
    <ul class="contacts">
      <li><svg viewBox="0 0 24 24"><path d="M6.6 10.8a15 15 0 0 0 6.6 6.6l2.2-2.2a1 1 0 0 1 1-.25 11 11 0 0 0 3.6.6 1 1 0 0 1 1 1V20a1 1 0 0 1-1 1A17 17 0 0 1 3 4a1 1 0 0 1 1-1h3.5a1 1 0 0 1 1 1 11 11 0 0 0 .6 3.6 1 1 0 0 1-.25 1z"/></svg>907 555 0184</li>
      <li><svg viewBox="0 0 24 24"><path d="M7 1h10a2 2 0 0 1 2 2v18a2 2 0 0 1-2 2H7a2 2 0 0 1-2-2V3a2 2 0 0 1 2-2zm0 3v14h10V4zm5 15.5a1 1 0 1 0 0 2 1 1 0 0 0 0-2z"/></svg>907 555 0263</li>
      <li><svg viewBox="0 0 24 24"><path d="M2 5h20v14H2zm2 2v.5l8 5 8-5V7zm0 2.8V17h16V9.8l-8 5z"/></svg>daniel@haldenhome.com</li>
      <li><svg viewBox="0 0 24 24"><path d="M12 2a10 10 0 1 0 0 20 10 10 0 0 0 0-20zm-1 17.9A8 8 0 0 1 4.2 10L9 15v1a2 2 0 0 0 2 2zm6.9-2.5A2 2 0 0 0 16 16h-1v-3a1 1 0 0 0-1-1H8v-2h2a1 1 0 0 0 1-1V7h2a2 2 0 0 0 2-2v-.4a8 8 0 0 1 2.9 12.8z"/></svg>www.haldenhome.com</li>
    </ul>
  </section>

  <section class="card card--back">
    <div class="back-mark">
      <span class="back-mark__dot"></span>
      <span class="back-mark__name">Halden Home Security Inc.</span>
    </div>
  </section>
</main>
</body>
</html>
```